Foot and ankle surgeon requires a website design

I need a website where prospective and established patients can obtain information and then direct them to making appointments. My practice is a highly professional surgical practice specialising in surgery to the foot and ankle. My title is Mr Colin Brasket, Podiatric Foot & Ankle Surgeon. My qualifications are: BSc MSc FACPS
The practice website will require information on: Locations, phone numbers to make appointments, general background on podiatric surgery,
I would like to include information on: my hospital appointments, surgical fellowships held, training programs undertaken, association memberships, publications written, links to useful websites
A page dedicated to common foot conditions would be useful and also a page with referral information including an online registration section that will be sent direct to the receptionist.
Examples of similar websites include:
http://www.dorvelquintaro.com.au/
http://www.haldenfootsurgeon.com.au/
I will provide files on logo, self photos and my personal training history etc.
Also if there is going to be a background theme I personally am associated with surfing and beach activities, it would be great if this was able to be reflected in the design.
Thank you.

```html
<!DOCTYPE html>
<html lang="en">
<head>
<meta charset="utf-8">
<title>Mr Colin Brasket – Podiatric Foot &amp; Ankle Surgeon</title>
<link href="https://fonts.googleapis.com/css2?family=Roboto:wght@300;400;500;700&family=Open+Sans:wght@400&display=swap" rel="stylesheet">
<style>
:root{
  --navy:#1d4f82;
  --blue:#2f6595;
  --orange:#ee7a12;
  --orange-dark:#d0650a;
  --grey-band:#ececec;
  --text:#333;
  --footer-dark:#1c1c1c;
  --white:#fff;
}
*{margin:0;padding:0;box-sizing:border-box}
html,body{width:922px;height:1200px;overflow:hidden;background:var(--white);font-family:'Roboto',sans-serif;color:var(--text)}
.page{position:relative;width:922px;height:1200px}
.wrap{position:absolute;left:134px;width:659px}

/* header */
.brand{position:absolute;left:134px;top:12px;display:flex;align-items:center;gap:10px}
.brand-mark{width:36px;height:36px;border-radius:50%;border:3px solid var(--navy)}
.brand-name{font-size:15px;font-weight:500;color:var(--navy);line-height:1.2}
.brand-name span{display:block}
.contact-phone{position:absolute;right:131px;top:28px;font-size:17px;color:#222;display:flex;align-items:center;gap:8px}
.contact-addr{position:absolute;right:131px;top:64px;font-size:10.5px;color:#222;display:flex;align-items:center;gap:6px}

/* nav */
.nav{top:106px;height:41px;background:linear-gradient(#1f5a8e,#143f6b);display:flex}
.nav a{color:var(--white);text-decoration:none;font-size:10px;display:flex;align-items:center;padding:0 9px;border-right:1px solid rgba(255,255,255,.25)}
.nav a:last-child{border-right:none}
.nav a.active{background:var(--orange);padding:0 12px}

/* hero */
.hero{top:148px;height:334px;overflow:hidden}
.hero-photo{position:absolute;inset:0;background:
  radial-gradient(ellipse at 20% 30%,#f6e2a6 0%,#d9b064 30%,transparent 60%),
  linear-gradient(180deg,#c9b48a 0%,#8a9aa8 45%,#7d6a3c 70%,#5b4320 100%)}
.hero-title{position:absolute;left:73px;top:90px;color:var(--navy)}
.hero-title .light{display:block;font-size:29px;font-weight:300}
.hero-title .bold{display:block;font-size:32px;font-weight:400;margin-top:4px;letter-spacing:.5px}
.hero-dots{position:absolute;left:627px;top:110px;display:flex;flex-direction:column;gap:4px}
.hero-dots i{width:10px;height:10px;border-radius:50%;background:var(--white)}
.hero-dots i.on{background:var(--orange)}

/* cta */
.cta{top:482px;height:78px;background:var(--grey-band)}
.cta-text{position:absolute;left:31px;top:29px;font-size:16.5px;color:#333}
.btn{display:inline-flex;align-items:center;justify-content:center;color:var(--white);background:linear-gradient(var(--orange),var(--orange-dark));border-radius:3px;box-shadow:0 2px 0 #b85608;font-weight:700}
.cta .btn{position:absolute;left:463px;top:16px;width:166px;height:42px;font-size:16px}

/* welcome */
.h2{font-size:17px;font-weight:500;color:var(--navy)}
.welcome{top:580px;width:442px}
.welcome .lead{margin-top:16px;font-size:10px;line-height:20px;text-transform:uppercase}
.welcome .body{margin-top:7px;font-size:11.5px;line-height:18px}
.welcome .btn{margin-top:22px;width:101px;height:29px;font-size:11px}

.treatments{top:580px;left:616px;width:180px}
.treatments ul{list-style:none;margin-top:17px}
.treatments li{display:flex;align-items:center;gap:11px;height:25px;font-size:10.5px;color:var(--navy);text-transform:uppercase}

/* conditions */
.conditions{top:799px}
.cond-grid{display:flex;gap:5.5px;margin-top:10px}
.cond{width:160px;text-align:center}
.cond-img{height:101px;border:1px solid #cfd6dc;background:radial-gradient(ellipse at center,#3f8fd0 0%,#8fbde0 35%,#e8f0f6 70%)}
.cond p{margin-top:10px;font-size:12px;color:var(--navy)}

/* footer */
.footer{position:absolute;left:0;top:976px;width:922px;height:166px;background:var(--blue);color:var(--white)}
.f-title{position:absolute;font-size:12px;font-weight:400;text-transform:uppercase}
.loc{position:absolute;top:64px;font-size:8.2px;line-height:12px}
.loc h4{font-size:8.5px;font-weight:500;margin-bottom:9px}
.news-input{position:absolute;left:514px;top:64px;width:116px;height:28px;background:var(--white);border:1px solid #bbb;font:italic 8px 'Roboto',sans-serif;color:#888;padding-left:8px;display:flex;align-items:center}
.footer .btn{position:absolute;left:514px;top:102px;width:73px;height:21px;font-size:9.5px;font-weight:400}
.social{position:absolute;left:681px;top:62px;list-style:none}
.social li{display:flex;align-items:center;gap:7px;height:23px;font-size:10.5px}
.social i{width:19px;height:19px;border-radius:2px;background:#1f3f60}
.bottom{position:absolute;left:0;top:1142px;width:922px;height:58px;background:var(--footer-dark);color:var(--white);font:9.5px 'Open Sans',sans-serif;display:flex;align-items:center;justify-content:center}
</style>
</head>
<body>
<div class="page">

  <header>
    <div class="brand">
      <div class="brand-mark"></div>
      <div class="brand-name"><span>Mr Colin Brasket</span><span>Podiatric Foot &amp; Ankle Surgeon</span></div>
    </div>
    <div class="contact-phone">
      <svg width="16" height="16" viewBox="0 0 24 24"><path fill="#ee7a12" d="M6.6 10.8a15 15 0 0 0 6.6 6.6l2.2-2.2a1 1 0 0 1 1-.3 11 11 0 0 0 3.6.6 1 1 0 0 1 1 1V20a1 1 0 0 1-1 1A17 17 0 0 1 3 4a1 1 0 0 1 1-1h3.5a1 1 0 0 1 1 1c0 1.3.2 2.5.6 3.6a1 1 0 0 1-.3 1z"/></svg>
      08 9174 2265
    </div>
    <div class="contact-addr">
      <svg width="10" height="14" viewBox="0 0 10 14"><path fill="#ee7a12" d="M5 0a5 5 0 0 0-5 5c0 3.6 5 9 5 9s5-5.4 5-9a5 5 0 0 0-5-5zm0 7a2 2 0 1 1 0-4 2 2 0 0 1 0 4z"/></svg>
      48 Harbour View Road PO BOX 2217 Seacliff WA 6532
    </div>
  </header>

  <nav class="wrap nav">
    <a class="active">Home</a><a>Appointments</a><a>Surgical Fellowships</a><a>Training programs</a><a>Memberships</a><a>Publications</a><a>Useful websites</a><a>Contact us</a>
  </nav>

  <section class="wrap hero">
    <div class="hero-photo" role="img" aria-label="Runner's legs in trail shoes striding across a grassy hilltop under a golden sky"></div>
    <h1 class="hero-title"><span class="light">FOOT</span><span class="bold">KNOWLEDGE</span></h1>
    <div class="hero-dots"><i></i><i class="on"></i><i></i><i></i><i></i></div>
  </section>

  <section class="wrap cta">
    <p class="cta-text">REQUEST AN APPOINTMENT CLICK HERE</p>
    <a class="btn">APPOINTMENTS</a>
  </section>

  <section class="wrap welcome">
    <h2 class="h2">WELCOME TO&nbsp; MR COLIN BRASKET</h2>
    <p class="lead">The ankle and foot health group strive to provide exceptional service and care to all patients, young and old, to ensure they enjoy a pain free lifestyle</p>
    <p class="body">For those unfamiliar with our services, we are a team of accredited health professionals dealing with the prevention, diagnosis, treatment and rehabilitation of medical and surgical conditions related to feet, ankles and lower limbs</p>
    <a class="btn">READ MORE</a>
  </section>

  <section class="wrap treatments">
    <h2 class="h2">TREATMENTS</h2>
    <ul>
      <li><svg width="12" height="12" viewBox="0 0 12 12"><circle cx="6" cy="6" r="6" fill="#ee7a12"/><path d="M3.3 6.2l1.8 1.8 3.6-3.6" stroke="#fff" stroke-width="1.5" fill="none"/></svg>Digital gait analysis</li>
      <li><svg width="12" height="12" viewBox="0 0 12 12"><circle cx="6" cy="6" r="6" fill="#ee7a12"/><path d="M3.3 6.2l1.8 1.8 3.6-3.6" stroke="#fff" stroke-width="1.5" fill="none"/></svg>Foot &amp; ankle surgery</li>
      <li><svg width="12" height="12" viewBox="0 0 12 12"><circle cx="6" cy="6" r="6" fill="#ee7a12"/><path d="M3.3 6.2l1.8 1.8 3.6-3.6" stroke="#fff" stroke-width="1.5" fill="none"/></svg>Sports injuries</li>
      <li><svg width="12" height="12" viewBox="0 0 12 12"><circle cx="6" cy="6" r="6" fill="#ee7a12"/><path d="M3.3 6.2l1.8 1.8 3.6-3.6" stroke="#fff" stroke-width="1.5" fill="none"/></svg>Air cast support braces</li>
      <li><svg width="12" height="12" viewBox="0 0 12 12"><circle cx="6" cy="6" r="6" fill="#ee7a12"/><path d="M3.3 6.2l1.8 1.8 3.6-3.6" stroke="#fff" stroke-width="1.5" fill="none"/></svg>Online appointments</li>
      <li><svg width="12" height="12" viewBox="0 0 12 12"><circle cx="6" cy="6" r="6" fill="#ee7a12"/><path d="M3.3 6.2l1.8 1.8 3.6-3.6" stroke="#fff" stroke-width="1.5" fill="none"/></svg>Custom foot orthotics</li>
    </ul>
  </section>

  <section class="wrap conditions">
    <h2 class="h2">FOOT CONDITIONS</h2>
    <div class="cond-grid">
      <div class="cond"><div class="cond-img" role="img" aria-label="Blue x-ray style view of the front of a foot"></div><p>ANTERIOR FOOT</p></div>
      <div class="cond"><div class="cond-img" role="img" aria-label="Blue x-ray style view of the inner side of a foot"></div><p>MEDIAL FOOT</p></div>
      <div class="cond"><div class="cond-img" role="img" aria-label="Blue x-ray style view of the outer side of a foot"></div><p>LATERAL FOOT</p></div>
      <div class="cond"><div class="cond-img" role="img" aria-label="Blue x-ray style view of the sole of a foot"></div><p>SOLE OF FOOT</p></div>
    </div>
  </section>

  <footer class="footer">
    <h3 class="f-title" style="left:136px;top:33px">Our Locations</h3>
    <div class="loc" style="left:139px"><h4>SEACLIFF</h4>48 Harbour View<br>Road, PO BOX 2217,<br>Seacliff WA 6532<br>Ph: 08 9931 5520<br>Fax: 08 9931 5521</div>
    <div class="loc" style="left:260px"><h4>WEST END, SEACLIFF</h4>7A &amp; 7B Tidewater Street,<br>Seacliff 6532.<br>Ph: 9931 7740<br>Fax: 9931 7741</div>
    <div class="loc" style="left:398px"><h4>REDSTONE</h4>3/14 Ironbark St,<br>Redstone WA 6436<br>Ph: 08 9174 2265<br>Fax: 08 9174 2266</div>
    <h3 class="f-title" style="left:515px;top:31px">Newsletter</h3>
    <div class="news-input">Enter Your Mail Id</div>
    <a class="btn">Subscribe</a>
    <h3 class="f-title" style="left:681px;top:31px">Connect With Us</h3>
    <ul class="social">
      <li><i></i>Friendbook</li>
      <li><i></i>Chirper</li>
      <li><i></i>ProLink</li>
    </ul>
  </footer>
  <div class="bottom">Copyright © 2014 All rights reserved</div>

</div>
</body>
</html>
```